Wordpress Design Project SEO/SEM Website

Need an updated more professional look for an SEO/SEM existing site.
see: www.brightquill-hub.com

I have an existing logo (in eps format), but am flexible on color and would consider updating the logo if the current colors or design limits your creativity.

Target Market(s)

My customers tend to be marketing managers for mid-size companies with 50+ employees.

Industry/Entity Type

Marketing

Requirements
Must have
• Design should support WordPress 3.0 menus, and widgets.
Nice to have
• Should you want/need it, the font used in the logo is 'ARTLOOKIN'
Should not have
• flash

```html
<!DOCTYPE html>
<html lang="en">
<head>
<meta charset="utf-8">
<title>Brightquill Hub – Internet Marketing</title>
<link href="https://fonts.googleapis.com/css2?family=Cinzel:wght@400&family=PT+Sans:wght@400;700&display=swap" rel="stylesheet">
<style>
:root{
  --teal-deep:#0a4a66;
  --teal:#0f6387;
  --teal-light:#2286ad;
  --page:#f5f5f5;
  --card:#e2e2e2;
  --side-head:#cfcfcf;
  --text:#555;
  --text-dark:#222;
  --rule:#d6d6d6;
  --white:#fff;
}
*{box-sizing:border-box;margin:0;padding:0}
html,body{width:969px;height:1200px;overflow:hidden}
body{position:relative;font-family:"PT Sans",Arial,sans-serif;color:var(--text);
  background:radial-gradient(ellipse at 50% 40%,#1c7398 0%,#0e5676 55%,#093f58 100%)}
a{color:inherit;text-decoration:none}
.abs{position:absolute}
.toplinks{position:absolute;top:14px;right:54px;display:flex;gap:18px;color:var(--white);font-size:13px;align-items:center}
.toplinks span{display:flex;align-items:center;gap:8px}
.toplinks i{display:inline-block;width:16px;height:16px;border-radius:3px}
.page{position:absolute;left:38px;top:44px;width:894px;height:1066px;background:var(--page);box-shadow:0 0 8px rgba(0,0,0,.4)}
.brand{left:15px;top:12px;display:flex;gap:18px;align-items:flex-start}
.brand-mark{width:80px;height:80px;border-radius:50%;background:var(--teal);margin-top:10px}
.brand-name{font-family:"Cinzel",serif;font-size:31px;line-height:33px;color:#9a9a9a;letter-spacing:1px;margin-top:8px}
.brand-tag{font-size:13px;color:#777;margin-top:10px}
.call{right:18px;top:48px;font-size:16px;color:var(--text-dark)}
.member{right:18px;top:87px;font-size:12px;color:var(--text-dark);display:flex;align-items:center;gap:8px}
.badge{width:94px;height:21px;background:linear-gradient(90deg,#e8e8e8,#8a8a8a);border:1px solid #aaa}
.nav{left:3px;top:131px;width:888px;height:47px;background:linear-gradient(#1a6e92,#0c5577);display:flex;align-items:center;font-size:14px;color:var(--white)}
.nav a{padding:0 19px;height:47px;line-height:47px}
.nav a.active{background:linear-gradient(#2a8bb3,#13668a);width:92px;text-align:center;padding:0}
.search{position:absolute;right:14px;top:12px;width:171px;height:22px;background:var(--white);border:1px solid #ccc;font-size:12px;color:#888;line-height:20px;padding-left:8px}
.search svg{position:absolute;right:3px;top:2px}
.slider{left:3px;top:182px;width:888px;height:227px;border:1px solid #ccc;background:linear-gradient(90deg,#c9d9e6 0%,#e7eef4 30%,#f4f6f8 60%,#fafafa 100%)}
.slide-photo{position:absolute;left:80px;top:0;width:370px;height:225px;background:linear-gradient(#dfe7ee,#9aa8b6 60%,#232a36 100%)}
.slide-title{left:531px;top:62px;font-size:27px;color:#777}
.slide-sub{left:532px;top:101px;font-size:15.5px;line-height:22px;color:#888}
.arrow{top:96px;width:33px;height:33px;border-radius:50%;background:linear-gradient(#d5d5d5,#8f8f8f);border:2px solid #eee}
.crumb{left:3px;top:413px;width:888px;height:40px;background:var(--teal);color:var(--white);font-size:14px;line-height:40px;padding-left:14px}
.intro{left:198px;top:470px;width:420px}
.intro h1{font-size:17px;font-weight:400;color:var(--teal);padding-bottom:6px;border-bottom:2px solid var(--teal)}
.intro p{font-size:12px;line-height:17px;margin-top:8px}
.intro p+p{line-height:20px;margin-top:5px}
.card{width:284px;height:118px;background:var(--card);border-top:3px solid var(--teal-deep)}
.card h2{position:absolute;left:8px;top:12px;font-size:14px;font-weight:400;color:var(--teal)}
.card p{position:absolute;left:10px;top:39px;width:150px;font-size:12px;line-height:16.7px}
.card p b{font-weight:400;color:var(--text-dark)}
.card .pic{position:absolute;right:5px;top:6px;width:103px;height:102px}
.contact{left:18px;top:946px;width:589px;height:105px;background:#d3d3d3;font-size:13px}
.contact h3{position:absolute;left:12px;top:14px;font-size:14px;font-weight:400;color:var(--text-dark)}
.contact address{position:absolute;left:13px;top:40px;font-style:normal;line-height:19px;color:var(--text)}
.c-line{position:absolute;left:220px;font-size:13px;color:var(--text-dark)}
.c-line span{color:var(--text);margin-left:8px}
.connect{position:absolute;left:376px;top:40px;color:var(--text-dark)}
.dots{position:absolute;left:376px;top:64px;display:flex;gap:13px}
.dot{width:24px;height:24px;border-radius:50%;background:var(--white);border:1px solid #bbb}
.contact .portrait{position:absolute;right:0;bottom:0;width:68px;height:85px;background:linear-gradient(#d0c8c0,#b08a78 55%,#222 80%)}
.side{left:641px;width:248px}
.side h4{height:33px;line-height:33px;background:var(--side-head);font-size:14px;font-weight:400;color:var(--text-dark);padding-left:11px}
.side ul{list-style:none;padding:10px 12px 10px;border-bottom:2px solid var(--rule)}
.side li{margin-bottom:12px}
.side li a{font-size:12px;color:var(--text-dark);text-decoration:underline}
.side li em{display:block;font-size:11px;color:#444;margin-top:3px}
.cats li{padding-left:14px;position:relative;font-size:12px;margin-bottom:10px;color:var(--text-dark)}
.cats li::before{content:"";position:absolute;left:2px;top:4px;border-left:5px solid #333;border-top:4px solid transparent;border-bottom:4px solid transparent}
.share{left:657px;top:1008px;display:flex;gap:8px;align-items:center;font-size:13px}
.share span{display:flex;align-items:center;gap:4px;color:var(--teal)}
.share i{display:inline-block;width:14px;height:14px;background:var(--teal)}
.btn{border:1px solid #aaa;background:linear-gradient(#fff,#ddd);padding:1px 5px;font-size:11px;color:#333;font-weight:700}
.footer-links{left:58px;top:1127px;font-size:12px;color:var(--white);word-spacing:4px}
.copyright{left:58px;top:1161px;font-size:12px;color:var(--white)}
.foot-dots{left:786px;top:1138px;display:flex;gap:13px}
.foot-dots .dot{border-color:#cde}
</style>
</head>
<body>
<div class="toplinks">
  <span><i style="background:#d94b3a"></i>E mail</span>
  <span><i style="background:#e98a22"></i>RSS</span>
  <span><i style="background:#8a7a6a;border-radius:50%"></i>Member Login</span>
</div>

<div class="page">
  <header class="brand abs">
    <div class="brand-mark"></div>
    <div>
      <div class="brand-name">BRIGHTQUILL<br>HUB</div>
      <div class="brand-tag">Internet Marketing, Riverton Alabama 35990</div>
    </div>
  </header>
  <div class="call abs">Call Us : 555 - 013 - 2840</div>
  <div class="member abs">Member on : <div class="badge"></div></div>

  <nav class="nav abs">
    <a class="active" href="#">Home</a><a href="#">Services</a><a href="#">SEO</a><a href="#">SEM</a><a href="#">About Us</a><a href="#">Contact Us</a>
    <div class="search">Search
      <svg width="18" height="18" viewBox="0 0 18 18"><circle cx="8" cy="8" r="5.5" fill="none" stroke="#777" stroke-width="1.6"/><line x1="12" y1="12" x2="16" y2="16" stroke="#777" stroke-width="2"/></svg>
    </div>
  </nav>

  <section class="slider abs">
    <div class="slide-photo" role="img" aria-label="Smiling businesswoman seated at a desk in a bright office"></div>
    <div class="arrow abs" style="left:11px"></div>
    <div class="arrow abs" style="right:11px"></div>
    <div class="slide-title abs">Boluptatem</div>
    <div class="slide-sub abs">Accusantium doloremque laudantium<br>totamrem aperiam eaque</div>
  </section>

  <div class="crumb abs">Home &gt; Internet Marketing</div>

  <svg class="abs" style="left:8px;top:480px" width="178" height="148" viewBox="0 0 178 148">
    <circle cx="86" cy="48" r="46" fill="#2a8ab8" opacity=".9"/>
    <circle cx="46" cy="98" r="46" fill="#9aab3c" opacity=".9"/>
    <circle cx="128" cy="98" r="46" fill="#c87a2e" opacity=".9"/>
    <g fill="#fff" font-family="PT Sans,Arial,sans-serif" font-size="13" text-anchor="middle">
      <text x="86" y="48">Content</text>
      <text x="46" y="96">Incoming</text><text x="46" y="110">Links</text>
      <text x="130" y="96">Site</text><text x="130" y="110">Architecture</text>
    </g>
  </svg>

  <article class="intro abs">
    <h1>Internet Marketing</h1>
    <p>Brightquill Hub provides Search Engine Optimization (SEO) and Search Engine Marketing (SEM) services for the Riverton Alabama area. Our focus is optimizing and marketing websites to maximize results.</p>
    <p>Searchly's algorithm employs over 200 variables in determining the ranking of sites. At the core of the algorithm are three elements: Quality Content, Site Architecture, and Incoming Links.</p>
  </article>

  <div class="card abs" style="left:18px;top:658px"><h2>Quality Content</h2><p>Your site's content must convey its purpose in a clear fashion and, within seconds, convince... <b>more</b></p><div class="pic" role="img" aria-label="Hand writing with a pen" style="background:linear-gradient(135deg,#cfe3f2,#f1e2d2)"></div></div>
  <div class="card abs" style="left:323px;top:658px"><h2>Site Architecture</h2><p>The architecture of your site should convey in hierarchical fashion the relationship and importance ... <b>more</b></p><div class="pic" role="img" aria-label="Stacked website screens" style="background:linear-gradient(135deg,#fff,#c4d0e4 60%,#5a6a9a)"></div></div>
  <div class="card abs" style="left:18px;top:806px"><h2>Incoming Links</h2><p>The quality and quantity of incoming links are at the core of Searchly's Link Rank algo-rithm... <b>more</b></p><div class="pic" role="img" aria-label="Network of linked figures" style="background:radial-gradient(circle,#6bb6e4,#fff 70%)"></div></div>
  <div class="card abs" style="left:323px;top:806px"><h2>Freshness</h2><p>The freshness (or recency) of your content is also a factor in how your content ranks in the search results... <b>more</b></p><div class="pic" role="img" aria-label="Fresh green apple" style="background:radial-gradient(circle,#9ccc4a,#fff 70%)"></div></div>

  <section class="contact abs">
    <h3>Contact Us</h3>
    <address>Brightquill Hub<br>418 Larkspur Avenue<br>Riverton, AL 35992</address>
    <div class="c-line" style="top:40px">Call Us<span>555-013-2840</span></div>
    <div class="c-line" style="top:70px">Mail to<span>info@brightquill.co</span></div>
    <div class="connect">Connect with us</div>
    <div class="dots"><div class="dot"></div><div class="dot"></div><div class="dot"></div><div class="dot"></div></div>
    <div class="portrait" role="img" aria-label="Portrait of the company owner"></div>
  </section>

  <aside class="side abs" style="top:460px">
    <h4>Recent Posts</h4>
    <ul>
      <li><a href="#">Sedut perspiciatis unde omniste natus</a><em>February 6th, 2012</em></li>
      <li><a href="#">Sedut perspiciatis unde omniste natus</a><em>February 6th, 2012</em></li>
      <li><a href="#">Sedut perspiciatis unde omniste natus</a><em>February 6th, 2012</em></li>
    </ul>
  </aside>
  <aside class="side abs" style="top:664px">
    <h4>Recent Comments</h4>
    <ul>
      <li><a href="#">Sedut perspiciatis unde omniste natus</a><em>February 6th, 2012</em></li>
      <li><a href="#">Sedut perspiciatis unde omniste natus</a><em>February 6th, 2012</em></li>
      <li><a href="#">Sedut perspiciatis unde omniste natus</a><em>February 6th, 2012</em></li>
    </ul>
  </aside>
  <aside class="side abs" style="top:868px">
    <h4>Posts by Category</h4>
    <ul class="cats">
      <li><a href="#" style="text-decoration:underline">SEM Riverton</a> <em style="display:inline;font-size:11px">(44)</em></li>
      <li><a href="#" style="text-decoration:underline">SEO Riverton</a> (46)</li>
      <li><a href="#" style="text-decoration:underline">Web Analytics</a> (26)</li>
    </ul>
  </aside>
  <div class="share abs">
    <span><i></i>Circlepage</span>
    <span class="btn">Share</span>
    <span class="btn">Post</span>
    <span class="btn" style="font-weight:400">0</span>
  </div>
</div>

<div class="footer-links abs">Home &nbsp;| &nbsp;Services &nbsp;| &nbsp;Seo &nbsp;| &nbsp;SEm &nbsp;| &nbsp;About Us &nbsp;| &nbsp;Contact Us &nbsp;| &nbsp;Log in &nbsp;| &nbsp;FAQ &nbsp;| &nbsp;Sitemap</div>
<div class="copyright abs">Copyright © 2012 Brightquill Hub, LLC</div>
<div class="foot-dots abs"><div class="dot"></div><div class="dot"></div><div class="dot"></div><div class="dot"></div></div>
</body>
</html>
```